ambitious event and festival agency from austria needs fresh business card design

A new design is due for the new headquarters and the new challenges. We organize events for different target groups from 16 to 60 years. The design should therefore be straightforward and not confused, so we are open to new colors and the logo may also be changed. In general, however, the most interesting suggestions are the most interesting ones. after this order we are looking for more graphics for brightloom facebook instagramm homepage etc A new design is due for the new headquarters and the new challenges. We organize events for different target groups from 16 to 60 years. The design should therefore be straightforward and not confused, so we are open to new colors and the logo may also be changed. In general, however, the most interesting suggestions are the most interesting ones. after this order we are looking for more graphics for brightloom facebook instagramm homepage etc A new design is due for the new headquarters and the new challenges. We organize events for different target groups from 16 to 60 years. The design should therefore be straightforward and not confused, so we are open to new colors and the logo may also be changed. In general, however, the most interesting suggestions are the most interesting ones. after this order we are looking for more graphics for brightloom facebook instagramm homepage etc
Updates

Reason: I am sorry for this decision but i need some more time. No new designs please, there are so many good ones and I will have made a decision in the next 3 days.

Target Market(s)

Industry/Entity Type

Business

Font styles to use
Serif
Sans Serif

Colors

Designer to choose colors to be used in the design.

Requirements
Must have
Nice to have
Should not have

```html
<!DOCTYPE html>
<html lang="en">
<head>
<meta charset="utf-8">
<title>brightloom business card</title>
<link rel="stylesheet" href="https://fonts.googleapis.com/css2?family=Roboto:wght@400;500&family=Roboto+Condensed:wght@400;700&display=swap">
<style>
  :root {
    --brand-red: #b02434;
    --brand-grey: #646b6e;
    --text-dark: #3f4446;
    --card-white: #f6f6f6;
    --backdrop: #e2e2e2;
    --rule: #5a5f61;
  }
  * { margin: 0; padding: 0; box-sizing: border-box; }
  html, body { width: 1200px; height: 960px; overflow: hidden; }
  body {
    position: relative;
    background: var(--backdrop);
    font-family: "Roboto", Arial, sans-serif;
  }
  .card {
    position: absolute;
    width: 602px;
    height: 343px;
    box-shadow: 1px 2px 4px rgba(0,0,0,0.35);
    overflow: hidden;
  }
  .card--front { left: 314px; top: 113px; background: var(--card-white); }
  .card--back { left: 311px; top: 472px; background: var(--brand-red); }

  .wordmark {
    position: absolute;
    font-family: "Roboto", Arial, sans-serif;
    font-weight: 500;
    letter-spacing: -1px;
    line-height: 1;
  }
  .card--front .wordmark {
    right: 42px; top: 44px;
    font-size: 46px;
    color: var(--brand-red);
  }
  .card--back .wordmark {
    left: 0; right: 0; top: 140px;
    text-align: center;
    font-size: 62px;
    color: #ffffff;
  }

  .holder { position: absolute; left: 38px; top: 186px; }
  .holder__name {
    font-family: "Roboto Condensed", Arial, sans-serif;
    font-weight: 700;
    font-size: 22px;
    color: var(--brand-red);
    line-height: 1;
  }
  .holder__role {
    font-family: "Roboto Condensed", Arial, sans-serif;
    font-size: 15.5px;
    color: var(--brand-grey);
    margin-top: 7px;
    letter-spacing: 0.3px;
  }
  .divider {
    position: absolute; left: 38px; top: 239px;
    width: 522px; height: 1px; background: var(--rule);
  }
  .contact {
    position: absolute; left: 38px; top: 255px;
    list-style: none;
    font-size: 14px; color: var(--text-dark); line-height: 19px;
  }
  .contact__item { display: flex; align-items: center; gap: 8px; }
  .contact__icon { width: 13px; height: 13px; fill: var(--brand-red); }
  .address {
    position: absolute; right: 40px; top: 256px;
    text-align: right;
    font-size: 14px; color: var(--text-dark); line-height: 19px;
  }
  .bands { position: absolute; left: 0; bottom: 0; width: 602px; height: 34px; }
  .site-link {
    position: absolute;
    color: #ffffff;
    font-size: 13.5px;
    letter-spacing: 3px;
  }
  .card--front .site-link { right: 34px; top: 317px; }
  .card--back .site-link {
    left: 0; right: 0; top: 289px;
    text-align: center; letter-spacing: 5px; font-size: 14px;
  }
</style>
</head>
<body>
  <section class="card card--front">
    <div class="wordmark">brightloom</div>

    <div class="holder">
      <p class="holder__name">MARKUS LEHNHARDT</p>
      <p class="holder__role">GESCHAFTSFUHRER</p>
    </div>
    <div class="divider"></div>

    <ul class="contact">
      <li class="contact__item">
        <svg class="contact__icon" viewBox="0 0 24 24" aria-hidden="true"><path d="M6.6 10.8c1.4 2.8 3.8 5.1 6.6 6.6l2.2-2.2c.3-.3.7-.4 1-.2 1.1.4 2.3.6 3.6.6.6 0 1 .4 1 1V20c0 .6-.4 1-1 1C10.6 21 3 13.4 3 4c0-.6.4-1 1-1h3.5c.6 0 1 .4 1 1 0 1.3.2 2.5.6 3.6.1.3 0 .7-.2 1z"/></svg>
        +43 650 418 273 5
      </li>
      <li class="contact__item">
        <svg class="contact__icon" viewBox="0 0 24 24" aria-hidden="true"><path d="M2 5h20v14H2z M2 5l10 7 10-7" fill="var(--brand-red)"/><path d="M3 6l9 6.3L21 6" fill="none" stroke="#f6f6f6" stroke-width="2"/></svg>
        m.lehnhardt@brightloom.eu
      </li>
    </ul>

    <address class="address" style="font-style:normal">
      Talgasse 12<br>A4560 kirchdorf
    </address>

    <svg class="bands" viewBox="0 0 602 34" aria-hidden="true">
      <rect x="0" y="13" width="350" height="8" fill="var(--brand-grey)"/>
      <path d="M0 21 H330 C340 21 345 2 365 2 H602 V34 H0 Z" fill="var(--brand-red)"/>
    </svg>
    <span class="site-link">www.brightloom.eu</span>
  </section>

  <section class="card card--back">
    <div class="wordmark">brightloom</div>
    <span class="site-link">www.brightloom.eu</span>
  </section>
</body>
</html>
```